New, modern business card for growing audiology practice

We need a new business card for our audiology practice. Our logo and website have recently changed (more modern) and we want our business cards to reflect this change.
We conduct hearing tests, perform earwax removals, and fit & dispense hearing aids to our patients. We are a family owned practice in which the owner is the one who works directly with the patient. I have attached logos in various formats to use, as well as two ideas I found on this website; as well as a scanned copy of our current logo. Good luck!

Industry/Entity Type

Business

Contact Information for Business Card

Company name: Tolvera Hearing Center
Provider name: Peter Wolstenby, Au.D. F/NSB
Phone number: (440) 683-5127
Address: 837 W. Lindell Ave. Brennock Falls, OH 44871
email: tolverahearing@postvane.com
website: tolverahearing.com

Colors
000000
aaaaaa
dbdbdb
cacaca
9bcb3c
afd23c
cadf82
b1b1b1

Requirements
Must have
• My card must include information in the "details" section. In the attached images, I found a few that I liked and I would like to model after - "brisky bouncin'" and "Sound Method Center".
• Must be horizontal.
• Must include logos provided. I uploaded them in various file formats and various ways.
• Must match logo font, if possible, if not, please get as close as you can.
Nice to have
• I really like the idea of having a color on one side with just the logo and company name and the contact information and provider name on the other side. I also really like the idea of having the main color dominating on the logo/company side with accent of that same color on the contact side of the card.
Should not have
• Must not be vertical.

```html
<!DOCTYPE html>
<html lang="en">
<head>
<meta charset="utf-8">
<title>Tolvera Hearing Center – Business Card</title>
<link rel="stylesheet" href="https://fonts.googleapis.com/css2?family=Questrial&family=Montserrat:wght@400;600&display=swap">
<style>
  :root {
    --backdrop: #cacaca;
    --card-light: #f4f4f4;
    --card-dark: #1d1d1d;
    --ink: #000000;
    --green: #9bcb3c;
    --green-deep: #7fae2c;
    --muted: #b1b1b1;
    --paper-text: #dbdbdb;
  }
  * { box-sizing: border-box; margin: 0; padding: 0; }
  html, body { width: 1200px; height: 834px; overflow: hidden; }
  body {
    background: var(--backdrop);
    font-family: "Montserrat", Arial, sans-serif;
    position: relative;
  }
  .card {
    position: absolute;
    width: 560px;
    height: 320px;
    left: 320px;
    box-shadow: 0 6px 18px rgba(0,0,0,0.18);
  }
  .card--front { top: 77px; background: var(--card-light); }
  .card--back { top: 437px; background: var(--card-dark); }

  .brand {
    position: absolute;
    display: flex;
    align-items: center;
    gap: 12px;
    font-family: "Questrial", "Century Gothic", sans-serif;
    text-transform: uppercase;
    letter-spacing: -0.5px;
    white-space: nowrap;
  }
  .brand__dot {
    width: 14px; height: 14px;
    border-radius: 50%;
    background: var(--green);
  }
  .card--front .brand { left: 92px; top: 138px; font-size: 31px; color: var(--ink); }
  .card--back .brand { left: 44px; top: 62px; font-size: 24px; color: #ffffff; }

  .front-web {
    position: absolute;
    right: 92px; bottom: 58px;
    font-size: 14px;
    color: var(--green-deep);
    letter-spacing: 0.3px;
  }

  .divider {
    position: absolute;
    left: 44px; top: 205px;
    width: 270px; height: 1px;
    background: var(--green);
  }
  .provider {
    position: absolute;
    right: 36px; top: 150px;
    text-align: right;
  }
  .provider__name {
    font-weight: 600;
    font-size: 15px;
    color: var(--green);
    margin-bottom: 14px;
  }
  .provider__address {
    font-size: 11px;
    line-height: 1.6;
    color: var(--muted);
  }
  .contacts {
    position: absolute;
    left: 44px; top: 222px;
    list-style: none;
    font-size: 12px;
    line-height: 1.75;
    color: var(--paper-text);
  }
</style>
</head>
<body>
  <section class="card card--front" aria-label="Card front">
    <div class="brand"><span class="brand__dot"></span>Tolvera Hearing Center</div>
    <p class="front-web">www.tolverahearing.com</p>
  </section>

  <section class="card card--back" aria-label="Card back">
    <div class="brand"><span class="brand__dot"></span>Tolvera Hearing Center</div>
    <div class="divider"></div>
    <div class="provider">
      <p class="provider__name">Peter Wolstenby, Au.D. F/NSB</p>
      <p class="provider__address">837 W. Lindell<br>Ave. Brennock Falls, OH 44871</p>
    </div>
    <ul class="contacts">
      <li>(440) 683-5127</li>
      <li>tolverahearing@postvane.com</li>
      <li>www.tolverahearing.com</li>
    </ul>
  </section>
</body>
</html>
```